Design a fun and engaging Social Media eBook

Graphic design job:

For initial concept stage, please provide some sample powerpoint designs of:
-A cover
-Section divides
-A few copy pages

We can then work on the full document which would be redesigning 22 pages of existing copy in word docs into the template.

Will be used to educate staff on Social Media.
We would like the design of the document to reflect the digital and social landscape. It should be fun and engaing.

Should demonstrate creativity, have social community focus, and be colourful and modern.

The audience is older people that need to be convinced about the benefits of social media and require some education / tips on how to use it. 40-60 year olds.

To be supplied to us in powerpoint.

Target Market(s)

Older staff that need to get the benefits of social media

Industry/Entity Type

Education

Requirements
Must have
• Must be supplied in Powerpoint.
Look modern, slick, cool, edgy

Look very "Quince" brand in simplicity and digital sense.
Reflect a 'digital' type of design

Combine all documents into one clean document / workbook.

(Don't worry will not be ised for powerpoint presentations, just want it in an edible document format - so lots of text on a slide is fine) Finished product will be a PDF
Nice to have
• Interactive in some way with click throughs or page turners

```html
<!DOCTYPE html>
<html lang="en">
<head>
<meta charset="utf-8">
<title>Building a community &amp; increasing your fans</title>
<link href="https://fonts.googleapis.com/css2?family=Source+Sans+3:wght@400;600&display=swap" rel="stylesheet">
<style>
  :root {
    --page-bg: #e6e7eb;
    --panel-bg: #ffffff;
    --panel-border: #c9cacd;
    --band-orange: #ffa400;
    --card-bg: #ffffff;
    --card-active-bg: #e9eee4;
    --card-border: #d6d6d6;
    --tab-shadow: #8c8c8c;
    --number-grey: #a8a8a8;
    --body-grey: #6a6a6a;
    --rule-grey: #9a9a9a;
    --footer-text: #4a4a4a;
    --icon-grey: #707070;
    --c-intro: #f3a10c;
    --c-content: #6b8a52;
    --c-overview: #ef7a78;
    --c-tips: #6c6c6c;
    --c-quiz: #3a8c97;
    --c-page: #4b5fa6;
    --c-profile: #df7b3f;
    --c-etiquette: #2c9ed8;
  }
  * { box-sizing: border-box; margin: 0; padding: 0; }
  html, body { width: 1200px; height: 901px; overflow: hidden; }
  body {
    background: var(--page-bg);
    font-family: "Source Sans 3", "Myriad Pro", sans-serif;
    position: relative;
  }
  .panel {
    position: absolute;
    left: 21px; top: 22px; width: 1161px; height: 792px;
    border: 1px solid var(--panel-border);
    border-radius: 11px;
    background: var(--panel-bg);
    overflow: hidden;
  }
  .panel-backdrop {
    position: absolute; left: 0; right: 0; top: 100px; bottom: 0;
    background:
      radial-gradient(ellipse 60% 50% at 85% 90%, #ececec 0%, rgba(236,236,236,0) 70%),
      radial-gradient(ellipse 50% 60% at 15% 40%, #efefef 0%, rgba(239,239,239,0) 70%),
      linear-gradient(180deg, #f7f7f7 0%, #eeeeee 100%);
  }
  .title-band {
    position: absolute; left: 0; right: 0; top: 59px; height: 41px;
    background: var(--band-orange);
    color: #fff;
    font-size: 24px; font-weight: 400;
    text-align: center; line-height: 41px;
    letter-spacing: 0.2px;
  }
  .tile { position: absolute; width: 257px; height: 260px; }
  .tile-shadow {
    position: absolute; left: 14px; right: 8px; bottom: -11px; height: 22px;
    background: var(--tab-shadow);
    clip-path: polygon(3% 0, 100% 0, 100% 100%, 0 100%);
    border-radius: 0 0 4px 4px;
  }
  .card {
    position: absolute; inset: 0;
    background: var(--card-bg);
    border: 1px solid var(--card-border);
    border-radius: 8px;
    box-shadow: 0 1px 3px rgba(0,0,0,0.12);
  }
  .card.is-active { background: var(--card-active-bg); }
  .card-head {
    position: absolute; left: 13px; right: 10px; top: 20px;
    display: flex; justify-content: space-between; align-items: flex-start;
  }
  .card-number { font-size: 19px; color: var(--number-grey); font-weight: 600; line-height: 24px; }
  .card-title {
    font-size: 20px; font-weight: 600; line-height: 24px;
    text-align: right; white-space: nowrap;
  }
  .card-title.is-small { font-size: 18px; line-height: 21px; }
  .card-rule {
    position: absolute; left: 20px; right: 20px; top: 81px;
    border-top: 1px dotted var(--rule-grey);
  }
  .card-body {
    position: absolute; left: 22px; right: 22px; top: 96px;
    font-size: 13.5px; line-height: 27px; color: var(--body-grey);
    text-align: center;
  }
  .t-intro { color: var(--c-intro); }
  .t-content { color: var(--c-content); }
  .t-overview { color: var(--c-overview); }
  .t-tips { color: var(--c-tips); }
  .t-quiz { color: var(--c-quiz); }
  .t-page { color: var(--c-page); }
  .t-profile { color: var(--c-profile); }
  .t-etiquette { color: var(--c-etiquette); }
  .footer-home { position: absolute; left: 62px; top: 826px; width: 38px; height: 34px; }
  .footer-label {
    position: absolute; left: 147px; top: 837px;
    font-size: 13.5px; color: var(--footer-text);
  }
</style>
</head>
<body>
  <main class="panel">
    <div class="panel-backdrop" role="img" aria-label="Soft grey sweeping line pattern in the background"></div>
    <h1 class="title-band">Building a community &amp; increasing your fans</h1>
  </main>

  <section class="tile" style="left:54px;top:174px">
    <div class="tile-shadow"></div>
    <article class="card">
      <div class="card-head"><span class="card-number">01</span><h2 class="card-title t-intro">Introduction</h2></div>
      <div class="card-rule"></div>
      <p class="card-body">Duis autem vel eum iriure dolor in hendrerit in vulputate velit esse molestie consequat, vel illum dolore eu feugiat nulla facilisis at vero eros et accumsan et iusto.</p>
    </article>
  </section>

  <section class="tile" style="left:333px;top:174px">
    <div class="tile-shadow"></div>
    <article class="card is-active">
      <div class="card-head"><span class="card-number">02</span><h2 class="card-title t-content">Creating Content</h2></div>
      <div class="card-rule"></div>
      <p class="card-body">Duis autem vel eum iriure dolor in hendrerit in vulputate velit esse molestie consequat, vel illum dolore eu feugiat nulla facilisis at vero eros et accumsan et iusto.</p>
    </article>
  </section>

  <section class="tile" style="left:614px;top:174px">
    <div class="tile-shadow"></div>
    <article class="card">
      <div class="card-head"><span class="card-number">03</span><h2 class="card-title t-overview">Social Media<br>Overview</h2></div>
      <div class="card-rule"></div>
      <p class="card-body">Duis autem vel eum iriure dolor in hendrerit in vulputate velit esse molestie consequat, vel illum dolore eu feugiat nulla facilisis at vero eros et accumsan et iusto.</p>
    </article>
  </section>

  <section class="tile" style="left:891px;top:174px">
    <div class="tile-shadow"></div>
    <article class="card">
      <div class="card-head"><span class="card-number">04</span><h2 class="card-title t-tips">Tips and pull-<br>out quotes</h2></div>
      <div class="card-rule"></div>
      <p class="card-body">Duis autem vel eum iriure dolor in hendrerit in vulputate velit esse molestie consequat, vel illum dolore eu feugiat nulla facilisis at vero eros et accumsan et iusto.</p>
    </article>
  </section>

  <section class="tile" style="left:54px;top:494px">
    <div class="tile-shadow"></div>
    <article class="card">
      <div class="card-head"><span class="card-number">05</span><h2 class="card-title t-quiz">Quick Social Media<br>Questionnaire</h2></div>
      <div class="card-rule"></div>
      <p class="card-body">Duis autem vel eum iriure dolor in hendrerit in vulputate velit esse molestie consequat, vel illum dolore eu feugiat nulla facilisis at vero eros et accumsan et iusto.</p>
    </article>
  </section>

  <section class="tile" style="left:333px;top:494px">
    <div class="tile-shadow"></div>
    <article class="card">
      <div class="card-head"><span class="card-number">06</span><h2 class="card-title is-small t-page">Creating Your<br>Company Circlebook Page</h2></div>
      <div class="card-rule"></div>
      <p class="card-body">Duis autem vel eum iriure dolor in hendrerit in vulputate velit esse molestie consequat, vel illum dolore eu feugiat nulla facilisis at vero eros et accumsan et iusto.</p>
    </article>
  </section>

  <section class="tile" style="left:614px;top:494px">
    <div class="tile-shadow"></div>
    <article class="card">
      <div class="card-head"><span class="card-number">07</span><h2 class="card-title t-profile">Create a Linkwork<br>Personal Profile</h2></div>
      <div class="card-rule"></div>
      <p class="card-body">Duis autem vel eum iriure dolor in hendrerit in vulputate velit esse molestie consequat, vel illum dolore eu feugiat nulla facilisis at vero eros et accumsan et iusto.</p>
    </article>
  </section>

  <section class="tile" style="left:891px;top:494px">
    <div class="tile-shadow"></div>
    <article class="card">
      <div class="card-head"><span class="card-number">08</span><h2 class="card-title t-etiquette">Social Media<br>Etiquette</h2></div>
      <div class="card-rule"></div>
      <p class="card-body">Duis autem vel eum iriure dolor in hendrerit in vulputate velit esse molestie consequat, vel illum dolore eu feugiat nulla facilisis at vero eros et accumsan et iusto.</p>
    </article>
  </section>

  <svg class="footer-home" viewBox="0 0 38 34" aria-label="Home">
    <polygon points="19,1 1,17 5,17 19,5 33,17 37,17" fill="var(--icon-grey)"/>
    <rect x="27" y="3" width="4" height="9" fill="var(--icon-grey)"/>
    <path d="M6 18 L19 7 L32 18 V33 H23 V23 H15 V33 H6 Z" fill="var(--icon-grey)"/>
  </svg>
  <p class="footer-label">Harbourline Wealth Partners</p>
</body>
</html>
```